Business card design and logo for hot water plumbing business

I need a logo and business card for my business which installs hot water heaters
Must have on front:
Bramblefield Hot Water Solutions
Gareth Pennick
0417382946

Either front or back:
gareth@bramblefieldhotwatersolutions.com.au
ABN 48276153094
Licence No 583214K

On the back in point form:
Supply and installation of
• electric storage
• gas storage/instantaneous
• heat pumps
• solar heaters

Iv provided 3 examples of cards I like but open to different ideas.

```html
<!DOCTYPE html>
<html lang="en">
<head>
<meta charset="utf-8">
<title>Bramblefield Hot Water Solutions – Business Card</title>
<link rel="stylesheet" href="https://fonts.googleapis.com/css2?family=Open+Sans:wdth,wght@75..100,400..700&display=swap">
<style>
  :root {
    --page-bg: #ececec;
    --card-bg: #ffffff;
    --blue: #1a92dc;
    --blue-dark: #0671bd;
    --blue-light: #3aa9ea;
    --mark: #5bb8ec;
    --ink: #3b3b3b;
    --ink-soft: #222222;
    --white: #ffffff;
  }
  * { box-sizing: border-box; margin: 0; padding: 0; }
  html, body {
    width: 1200px; height: 899px; overflow: hidden;
    background: var(--page-bg);
    font-family: "Open Sans", Arial, sans-serif;
  }
  .stage { position: relative; width: 1200px; height: 899px; }
  .card {
    position: absolute; width: 670px; height: 383px;
    background: var(--card-bg); overflow: hidden;
    box-shadow: 0 2px 6px rgba(0,0,0,0.12);
  }
  .card-front { left: 153px; top: 60px; }
  .card-back  { left: 374px; top: 456px; }
  .card-art { position: absolute; inset: 0; width: 100%; height: 100%; }

  .brand-mark {
    position: absolute; border-radius: 50%; background: var(--mark);
  }
  .card-front .brand-mark { left: 280px; top: 76px; width: 110px; height: 110px; }
  .card-back .brand-mark { left: 92px; top: 24px; width: 70px; height: 70px; }

  .brand-name {
    position: absolute; color: var(--ink); font-weight: 700; white-space: nowrap;
    font-stretch: 75%;
  }
  .card-front .brand-name {
    left: 0; width: 670px; top: 211px; text-align: center; font-size: 22px;
  }
  .card-back .brand-name { left: 40px; top: 105px; font-size: 13px; }

  .contact-band {
    position: absolute; left: 0; top: 299px; width: 670px; height: 54px;
    display: flex; color: var(--white); font-size: 28px; font-weight: 400;
  }
  .contact-band .person {
    width: 402px; background: var(--blue); padding-left: 92px;
    display: flex; align-items: center; letter-spacing: 0.5px;
  }
  .contact-band .phone {
    flex: 1; background: var(--blue-dark); padding-left: 41px;
    display: flex; align-items: center; letter-spacing: 1px;
  }

  .details {
    position: absolute; left: 38px; top: 152px;
    font-size: 16.8px; line-height: 21.5px; color: var(--ink-soft);
  }
  .services {
    position: absolute; right: 54px; top: 226px; text-align: right;
    color: var(--white); font-weight: 600;
  }
  .services h2 { font-size: 22px; font-weight: 600; line-height: 30px; }
  .services ul { list-style: none; font-size: 21px; line-height: 26.5px; }
  .services li::before { content: "\2022\00a0"; }
</style>
</head>
<body>
<main class="stage">

  <section class="card card-front" aria-label="Business card front">
    <svg class="card-art" viewBox="0 0 560 320" preserveAspectRatio="none" aria-hidden="true">
      <path d="M470 0 C505 30 535 70 560 110 L560 0 Z" fill="var(--blue)"/>
      <path d="M492 0 L560 0 L560 62 Z" fill="var(--blue-dark)"/>
      <path d="M560 62 L560 110 C548 92 535 74 520 58 Z" fill="var(--blue-light)"/>
    </svg>
    <span class="brand-mark" aria-hidden="true"></span>
    <p class="brand-name">Bramblefield Hot Water Solutions</p>
    <div class="contact-band">
      <span class="person">Gareth Pennick</span>
      <span class="phone">0417382946</span>
    </div>
  </section>

  <section class="card card-back" aria-label="Business card back">
    <svg class="card-art" viewBox="0 0 560 320" preserveAspectRatio="none" aria-hidden="true">
      <path d="M335 0 C400 25 465 62 515 110 L560 96 L560 0 Z" fill="var(--blue-light)"/>
      <path d="M430 0 L560 0 L560 96 L515 110 C500 60 470 25 430 0 Z" fill="var(--blue)"/>
      <path d="M48 320 C190 235 380 150 515 110 L560 96 L560 320 Z" fill="var(--blue)"/>
      <path d="M515 110 L560 96 L560 320 L430 320 C470 250 500 180 515 110 Z" fill="var(--blue-dark)"/>
    </svg>
    <span class="brand-mark" aria-hidden="true"></span>
    <p class="brand-name">Bramblefield Hot Water Solutions</p>
    <div class="details">
      <p>gareth@bramblefieldhotwatersolutions.com.au</p>
      <p>ABN 48276153094</p>
      <p>Licence No 583214K</p>
    </div>
    <div class="services">
      <h2>Supply and installation of</h2>
      <ul>
        <li>electric storage</li>
        <li>gas storage/instantaneous</li>
        <li>heat pumps</li>
        <li>solar heaters</li>
      </ul>
    </div>
  </section>

</main>
</body>
</html>
```